New Fitness Company looking for creative website design

I am building a new fitness matching service. To match customers looking for fitness services to professionals that meet their requirements

My business will have 5 different divisions and I would like to have tabs for each division

1. Matching client to trainer - I need to have video upload capability on the site
2. Corporate personal training services

-The site needs a shopping cart as well as payment capability.
- I am looking for the site to be bright and inviting as well as have clients and trainers going through some type of workout on the main page.
- I also need the capability to capture email addresses
- We are going to have a section that ask the customer questions to match up the trainer so that needs to be a part of the site
-Ability to have trainers rated in a 1 star to 5 stars as well as reviews
- Site should be inviting, bright and vibrant colors that catch the eye and is easy to use
- Similar sites for inspiration are www.zavrello.com where you give a description of how the service works, short video and various services.

Target Market(s)

mid income to high income, mix of female and male customers

Industry/Entity Type

Fitness

Coding

Coded - Design and coding required

Number of Pages Required

5+ page

Font styles to use
Serif
Sans Serif

Requirements
Must have
• Must have the logos that I provided in the website
Should not have
• Not looking for bodybuilders on website. This is for everyday people that are interested in staying in shape and working out. So active fit people will resonate with my prospects

```html
<!DOCTYPE html>
<html lang="en">
<head>
<meta charset="utf-8">
<title>Vantor Fitness</title>
<link href="https://fonts.googleapis.com/css2?family=Oswald:wght@400;500&family=Open+Sans:wght@400;600;700&display=swap" rel="stylesheet">
<style>
:root{
  --orange:#f39322;
  --green:#3aaa48;
  --green-dark:#2f9a3c;
  --ink:#2b2b2b;
  --muted:#666;
  --light:#f2f2f2;
  --footer:#3b3b3b;
  --footer-text:#cfcfcf;
  --white:#fff;
}
*{box-sizing:border-box;margin:0;padding:0}
html,body{width:1200px;height:2862px;overflow:hidden}
body{font-family:"Open Sans",Arial,sans-serif;color:var(--ink);background:var(--white);position:relative}
.heading{font-family:"Oswald",Arial,sans-serif;font-weight:400;text-transform:uppercase}
.btn{display:inline-block;font-family:"Oswald",Arial,sans-serif;text-transform:uppercase;color:var(--white);font-size:16px;text-align:center}

/* top bar */
.topbar{height:54px;border-bottom:1px solid #e5e5e5;display:flex;align-items:center;padding:0 76px;font-size:13px;color:#444}
.topbar .contact{flex:1}
.topbar .search{width:170px;height:32px;border:1px solid #ccc;font-size:11px;padding:8px 10px;color:#777}
.topbar .search-btn{width:36px;height:32px;background:var(--orange);display:flex;align-items:center;justify-content:center}
.topbar .login{margin-left:22px;background:var(--green);color:#fff;font-size:11px;font-weight:700;padding:9px 12px}

/* header */
.header{height:114px;display:flex;align-items:center;padding:0 76px}
.logo{display:flex;align-items:center;gap:10px;flex:1}
.logo .mark{width:34px;height:34px;border-radius:50%;background:var(--green)}
.logo .name{font-family:"Oswald",sans-serif;font-weight:500;font-size:30px;color:var(--green);letter-spacing:1px}
.nav{display:flex;gap:34px;font-family:"Oswald",sans-serif;font-size:15px;text-transform:uppercase;align-items:center}
.nav .active{color:var(--orange)}
.cart{display:flex;align-items:center;gap:16px;margin-left:30px;font-family:"Oswald",sans-serif;font-size:15px}
.cart .circle{width:46px;height:46px;border-radius:50%;border:1px solid #ccc;display:flex;align-items:center;justify-content:center}

/* hero */
.hero{height:427px;position:relative;background:linear-gradient(100deg,#6c8a3c 0%,#a6c45a 35%,#d8d0c4 60%,#7aa64a 100%)}
.hero .arrow{position:absolute;top:180px}
.dots{position:absolute;bottom:28px;left:556px;display:flex;gap:10px}
.dots span{width:14px;height:14px;border-radius:50%;background:#fff}
.dots span.on{background:var(--green)}

/* newsletter */
.newsletter{height:100px;background:var(--orange);display:flex;align-items:center;justify-content:center;gap:24px}
.newsletter h3{color:#fff;font-size:32px;margin-right:0}
.newsletter .field{width:360px;height:46px;background:#fff;font-size:13px;color:#555;padding:14px 16px}
.newsletter .btn{background:var(--green);width:166px;height:46px;line-height:46px;margin-left:20px;font-size:18px}

/* corporate */
.corporate{height:383px;position:relative;text-align:center}
.corporate .photo{position:absolute}
.corporate h2{font-size:38px;padding-top:40px}
.corporate p{width:640px;margin:18px auto 0;font-size:13px;line-height:29px;color:#555}
.corporate .btn{background:var(--orange);width:144px;height:44px;line-height:44px;margin-top:24px;font-size:17px}

/* matching */
.matching{height:395px;position:relative;background:linear-gradient(90deg,#2a2a2a,#5a5a5a 45%,#3a3a3a)}
.match-box{position:absolute;left:254px;top:48px;width:690px;height:295px;background:rgba(58,170,72,.92);text-align:center;color:#fff}
.match-box h2{font-size:34px;padding-top:48px}
.match-box p{font-size:13px;line-height:30px;width:610px;margin:14px auto 0}
.match-box .btn{background:#2b2b2b;width:148px;height:44px;line-height:44px;margin-top:22px;font-size:17px}

/* shop */
.shop{height:492px;text-align:center}
.shop h2{font-size:34px;padding-top:32px}
.products{display:flex;justify-content:center;gap:6px;margin-top:22px}
.product{width:266px;height:334px;background:#fff;border:1px solid #eee;box-shadow:0 1px 3px rgba(0,0,0,.06);text-align:left;padding:0 26px}
.product .img{height:190px;margin:0 -26px;background:radial-gradient(circle,#d9d9d9 0,#f7f7f7 60%)}
.product h4{font-family:"Oswald",sans-serif;font-weight:400;font-size:17px;margin-top:18px}
.product p{font-size:13px;line-height:24px;color:#555;margin-top:6px}
.product .buy{display:flex;align-items:center;gap:14px;margin-top:16px}
.product .price{font-family:"Oswald",sans-serif;color:var(--orange);font-size:21px}
.product .btn{background:var(--green);width:84px;height:32px;line-height:32px;font-size:13px}

/* trainer + faq */
.trainers{height:470px;background:var(--light);position:relative;padding:42px 76px 0}
.trainers h2{font-size:36px}
.slide-arrows{position:absolute;left:718px;top:56px;display:flex;gap:10px}
.cards{display:flex;gap:10px;margin-top:22px}
.card{width:224px;height:320px;background:#fff;text-align:center}
.card .img{height:180px;background:linear-gradient(#eef0f1,#d7dadc)}
.card h4{font-family:"Oswald",sans-serif;font-weight:400;font-size:16px;margin-top:22px}
.stars{margin-top:6px}
.card p{font-size:12px;line-height:22px;color:#555;margin-top:6px;padding:0 20px}
.faq{position:absolute;left:794px;top:42px;width:332px}
.faq h2{font-size:36px}
.faq .item{background:#fff;margin-top:10px;padding:0 14px;height:38px;display:flex;align-items:center;justify-content:space-between;font-family:"Oswald",sans-serif;font-size:16px;color:var(--green)}
.faq .item.open{height:150px;flex-direction:column;align-items:stretch;justify-content:flex-start;padding-top:10px;margin-top:22px}
.faq .item.open .q{display:flex;justify-content:space-between}
.faq .item.open p{font-family:"Open Sans",sans-serif;font-size:12px;line-height:21px;color:#555;margin-top:8px}

/* footer */
.footer{height:328px;background:var(--footer);color:var(--footer-text);display:flex;padding:38px 76px 0}
.footer h5{font-family:"Oswald",sans-serif;font-weight:400;font-size:16px;color:#fff;text-transform:uppercase}
.col-about{width:376px;font-size:13px;line-height:25px}
.col-about p{margin-top:16px}
.col-about a{display:block;margin-top:14px;color:var(--green);font-family:"Oswald",sans-serif;text-transform:uppercase;font-size:14px}
.col-results{width:385px}
.story{display:flex;gap:20px;margin-top:16px}
.story:first-of-type{margin-top:20px}
.story .sq{width:90px;height:84px;background:var(--green);flex:none}
.story p{font-size:12px;line-height:23px;font-style:italic}
.story span{color:var(--green);font-size:11px;text-transform:uppercase;font-style:normal}
.col-connect .social{display:flex;gap:8px;margin-top:14px}
.col-connect .social span{width:28px;height:28px;border-radius:50%;background:#5a5a5a;border:1px solid #777}
.col-connect .flogo{display:flex;align-items:center;gap:8px;margin-top:34px}
.col-connect .flogo i{width:24px;height:24px;border-radius:50%;background:var(--green)}
.col-connect .flogo b{font-family:"Oswald",sans-serif;font-weight:500;color:var(--green);font-size:22px}
.col-connect small{display:block;font-size:11px;line-height:24px;margin-top:12px}
</style>
</head>
<body>

<div class="topbar">
  <div class="contact">24/7 Customer Services: &#9990; 1-800-555-0142 &nbsp;|&nbsp; &#9993; info@vantorfitness.com</div>
  <div class="search">Search...</div>
  <div class="search-btn"><svg width="14" height="14" viewBox="0 0 14 14"><circle cx="6" cy="6" r="4.5" fill="none" stroke="#fff" stroke-width="2"/><line x1="9.5" y1="9.5" x2="13" y2="13" stroke="#fff" stroke-width="2"/></svg></div>
  <div class="login">LOG IN / JOIN &#9662;</div>
</div>

<header class="header">
  <div class="logo"><span class="mark"></span><span class="name">VANTOR FITNESS</span></div>
  <nav class="nav">
    <span class="active">Home</span><span>About Us</span><span>Fitness Training</span><span>Articles &amp; Videos</span><span>FAQ</span><span>Store</span><span>Contact Us</span>
  </nav>
  <div class="cart">
    <span class="circle"><svg width="20" height="18" viewBox="0 0 20 18"><path d="M1 2h3l2 9h10l2-7H5" fill="none" stroke="#444" stroke-width="1.8"/><circle cx="8" cy="15" r="1.6" fill="#444"/><circle cx="15" cy="15" r="1.6" fill="#444"/></svg></span>
    <span>$0.00</span>
  </div>
</header>

<section class="hero" role="img" aria-label="Group of smiling men and women doing a push-up workout together in a bright gym">
  <svg class="arrow" style="left:72px" width="22" height="70" viewBox="0 0 22 70"><polyline points="20,2 2,35 20,68" fill="none" stroke="#fff" stroke-width="2"/></svg>
  <svg class="arrow" style="right:72px" width="22" height="70" viewBox="0 0 22 70"><polyline points="2,2 20,35 2,68" fill="none" stroke="#fff" stroke-width="2"/></svg>
  <div class="dots"><span class="on"></span><span></span><span></span><span></span></div>
</section>

<section class="newsletter">
  <h3 class="heading">Newsletter Sign Up</h3>
  <div class="field">ENTER EMAIL ADDRESS</div>
  <span class="btn">Sign Up Now</span>
</section>

<section class="corporate">
  <div class="photo" role="img" aria-label="Older couple exercising with a blue fitness ball" style="left:50px;top:8px;width:180px;height:330px;background:linear-gradient(#d9dde0,#8fb6d8)"></div>
  <div class="photo" role="img" aria-label="Woman in pink top stretching on the floor" style="left:950px;top:80px;width:226px;height:240px;background:linear-gradient(#f0f0f0,#c9a0c4)"></div>
  <h2 class="heading">Corporate Personal Training</h2>
  <p>Aliquam molestie, mi et imperdiet euismod, dui purus auctor tellus, et interdum lacus lectus et ante. Sed accumsan sollicitudin sapien, sit amet adipiscing turpis gravida ac. In congue, neque ac lobortis volutpat, libero mauris varius mi, vitae suscipit ipsum ligula vitae risus. Duis aliquam nibh a dui iaculis viverra id a velit. Vivamus egestas risus in magna varius commodo. Sed semper viverra egestas. Etiam pretium porttitor lectus, vel ornare neque porta volutpat.</p>
  <span class="btn">Read More</span>
</section>

<section class="matching" role="img" aria-label="Dark gym scene with a woman and a man doing dynamic exercises">
  <div class="match-box">
    <h2 class="heading">Matching Client to Trainer</h2>
    <p>Aliquam molestie, mi et imperdiet euismod, dui purus auctor tellus, et interdum lacus lectus et ante. Sed accumsan sollicitudin sapien, sit amet adipiscing turpis gravida ac. In congue, neque ac lobortis volutpat, libero mauris varius mi, vitae suscipit ipsum ligula vitae risus.</p>
    <span class="btn">Watch a Video</span>
  </div>
</section>

<section class="shop">
  <h2 class="heading">Shop Fitness Products</h2>
  <div class="products">
    <div class="product"><div class="img" role="img" aria-label="Dumbbell set with weight plates"></div><h4>SUSPENDISSE</h4><p>Sed semper viverra egestas. Etiam pretium porttitor lectus</p><div class="buy"><span class="price">$0.00</span><span class="btn">Add to Cart</span></div></div>
    <div class="product"><div class="img" role="img" aria-label="Pink exercise ball, step platform and foam roller"></div><h4>SUSPENDISSE</h4><p>Sed semper viverra egestas. Etiam pretium porttitor lectus</p><div class="buy"><span class="price">$0.00</span><span class="btn">Add to Cart</span></div></div>
    <div class="product"><div class="img" role="img" aria-label="Three tubs of protein powder"></div><h4>SUSPENDISSE</h4><p>Sed semper viverra egestas. Etiam pretium porttitor lectus</p><div class="buy"><span class="price">$0.00</span><span class="btn">Add to Cart</span></div></div>
    <div class="product"><div class="img" role="img" aria-label="Jump rope with blue handles"></div><h4>SUSPENDISSE</h4><p>Sed semper viverra egestas. Etiam pretium porttitor lectus</p><div class="buy"><span class="price">$0.00</span><span class="btn">Add to Cart</span></div></div>
  </div>
</section>

<section class="trainers">
  <h2 class="heading">Trainer Rating</h2>
  <div class="slide-arrows">
    <svg width="12" height="20" viewBox="0 0 12 20"><polyline points="10,2 2,10 10,18" fill="none" stroke="#666" stroke-width="2.5"/></svg>
    <svg width="12" height="20" viewBox="0 0 12 20"><polyline points="2,2 10,10 2,18" fill="none" stroke="#666" stroke-width="2.5"/></svg>
  </div>
  <div class="cards">
    <div class="card"><div class="img" role="img" aria-label="Male trainer holding a clipboard"></div><h4>TRAINER NAME</h4><svg class="stars" width="90" height="16" viewBox="0 0 90 16" aria-label="4.5 stars"><g fill="#f39322"><polygon id="s" points="8,0 10,5.5 16,6 11.5,9.8 13,16 8,12.6 3,16 4.5,9.8 0,6 6,5.5"/><use href="#s" x="18"/><use href="#s" x="36"/><use href="#s" x="54"/></g><polygon points="80,0 82,5.5 88,6 83.5,9.8 85,16 80,12.6 75,16 76.5,9.8 72,6 78,5.5" fill="#f7c98e"/></svg><p>Sed semper viverra egestas. etiam pretium porttitor</p></div>
    <div class="card"><div class="img" role="img" aria-label="Female trainer in yellow top"></div><h4>TRAINER NAME</h4><svg class="stars" width="90" height="16" viewBox="0 0 90 16" aria-label="4.5 stars"><g fill="#f39322"><use href="#s"/><use href="#s" x="18"/><use href="#s" x="36"/><use href="#s" x="54"/></g><use href="#s" x="72" fill="#f7c98e"/></svg><p>Sed semper viverra egestas. etiam pretium porttitor</p></div>
    <div class="card"><div class="img" role="img" aria-label="Male trainer in black shirt"></div><h4>TRAINER NAME</h4><svg class="stars" width="90" height="16" viewBox="0 0 90 16" aria-label="4.5 stars"><g fill="#f39322"><use href="#s"/><use href="#s" x="18"/><use href="#s" x="36"/><use href="#s" x="54"/></g><use href="#s" x="72" fill="#f7c98e"/></svg><p>Sed semper viverra egestas. etiam pretium porttitor</p></div>
  </div>
  <div class="faq">
    <h2 class="heading">FAQ</h2>
    <div class="item open"><div class="q"><span>Rhoncus lectus nunc ac nulla?</span><span style="color:var(--orange)">&#9662;</span></div><p>Sed semper viverra egestas. etiam pretium porttitor. Aenean a nibh eget turpis vehicula tempus ac sed . Nunc consequat congue nulla eu imperdiet.</p></div>
    <div class="item"><span>Rhoncus lectus nunc ac sollicitudin?</span><span style="color:#333">&#9656;</span></div>
    <div class="item"><span>Rhoncus lectus ac sollicitudin?</span><span style="color:#333">&#9656;</span></div>
    <div class="item"><span>Rhoncus lectus nunc?</span><span style="color:#333">&#9656;</span></div>
    <div class="item"><span>Rhoncus lectus nunc ac sollicitudin?</span><span style="color:#333">&#9656;</span></div>
  </div>
</section>

<section class="newsletter">
  <h3 class="heading">Newsletter Sign Up</h3>
  <div class="field">ENTER EMAIL ADDRESS</div>
  <span class="btn">Sign Up Now</span>
</section>

<footer class="footer">
  <div class="col-about">
    <h5>About Vantor Fitness</h5>
    <p>Duis aliquam nibh a dui iaculis viverra id a velit. Vivamus egestas risus in magna varius commodo. Sed semper viverra egestas. Etiam pretium porttitor lectus, vel ornare neque porta volutpat. Aenean lacinia sodales eros, sit amet molestie enim consectetur eget...</p>
    <a>Read More</a>
  </div>
  <div class="col-results">
    <h5>Real People. Real Results.</h5>
    <div class="story"><span class="sq"></span><p>Duis aliquam nibh a dui iaculis viverra id a velit. Vivamus egestas risus in magna varius commodo.<br><span>Name goes here</span></p></div>
    <div class="story"><span class="sq"></span><p>Duis aliquam nibh a dui iaculis viverra id a velit. Vivamus egestas risus in magna varius commodo.<br><span>Name goes here</span></p></div>
  </div>
  <div class="col-connect">
    <h5>Connect Us</h5>
    <div class="social"><span></span><span></span><span></span><span></span><span></span><span></span></div>
    <div class="flogo"><i></i><b>VANTOR FITNESS</b></div>
    <small>COPYRIGHT ©2015. ALL RIGHTS RESERVED<br>TERMS &amp; CONDITIONS</small>
  </div>
</footer>

</body>
</html>
```